Freelance business trainer needs a new business card

My business is called Brontlearn. I provide training in the workplace on management, coaching and mentoring, and customer service topics for a variety of businesses, colleges and private training providers, and teach on management programs. I need a professional but eye catching business card. Business colours grey and orange. My name Marion Tadwick; Tel 07382 415067; email mtadwick@brontlearn.co.uk; website www.brontlearn.co.uk.
Happy to have some sort of logo on front and details on back or all on one side
Target Market(s)
SME businesses and colleges - workshops i run are for adults in the workplace
Industry/Entity Type
Training
Look and feel

```html
<!DOCTYPE html>
<html lang="en">
<head>
<meta charset="utf-8">
<title>Brontlearn – Business Card</title>
<link rel="stylesheet" href="https://fonts.googleapis.com/css2?family=Ubuntu:wght@400;500&family=Roboto:wght@400&display=swap">
<style>
  :root {
    --backdrop: #e9e9ee;
    --card-white: #f7f6f1;
    --card-grey: #6a6d6f;
    --watermark-grey: #62656a;
    --brand-orange: #e27719;
    --ink-dark: #1f1f1f;
    --text-light: #ffffff;
  }
  * { box-sizing: border-box; margin: 0; padding: 0; }
  html, body {
    width: 1200px;
    height: 800px;
    overflow: hidden;
    background: var(--backdrop);
  }
  .business-card {
    position: absolute;
    left: 150px;
    top: 110px;
    width: 900px;
    height: 580px;
    background: var(--card-grey);
    overflow: hidden;
    box-shadow: 0 14px 30px rgba(0, 0, 0, 0.22);
  }
  .header-band {
    position: absolute;
    left: 0;
    top: 0;
    width: 100%;
    height: 178px;
    background: var(--card-white);
  }
  .brand {
    position: absolute;
    left: 68px;
    top: 52px;
    display: flex;
    align-items: center;
    gap: 16px;
  }
  .brand-dot {
    width: 84px;
    height: 84px;
    border-radius: 50%;
    background: var(--brand-orange);
  }
  .brand-name {
    font-family: "Ubuntu", sans-serif;
    font-weight: 400;
    font-size: 54px;
    color: var(--ink-dark);
    letter-spacing: 0.5px;
  }
  .accent-rules {
    position: absolute;
    left: 440px;
    top: 96px;
    width: 460px;
    height: 20px;
  }
  .watermark-circle {
    position: absolute;
    left: 620px;
    top: 200px;
    width: 290px;
    height: 290px;
    border-radius: 50%;
    background: var(--watermark-grey);
  }
  .name-tab {
    position: absolute;
    left: 0;
    top: 232px;
    width: 430px;
    height: 76px;
    background: var(--card-white);
    box-shadow: 6px 10px 14px rgba(0, 0, 0, 0.28);
    display: flex;
    align-items: center;
    padding-left: 58px;
  }
  .person-name {
    font-family: "Ubuntu", sans-serif;
    font-weight: 400;
    font-size: 31px;
    color: var(--brand-orange);
  }
  .contact-list {
    position: absolute;
    left: 66px;
    top: 350px;
    list-style: none;
  }
  .contact-item {
    display: flex;
    align-items: center;
    height: 58px;
  }
  .contact-icon {
    width: 28px;
    height: 28px;
    margin-right: 44px;
    fill: var(--brand-orange);
  }
  .contact-text {
    font-family: "Roboto", sans-serif;
    font-size: 27px;
    color: var(--text-light);
    letter-spacing: 0.3px;
  }
</style>
</head>
<body>
  <article class="business-card">
    <header class="header-band">
      <div class="brand">
        <span class="brand-dot"></span>
        <span class="brand-name">Brontlearn</span>
      </div>
      <svg class="accent-rules" viewBox="0 0 460 20" preserveAspectRatio="none" aria-hidden="true">
        <line x1="0" y1="4" x2="460" y2="4" stroke="#e27719" stroke-width="3"/>
        <line x1="0" y1="16" x2="460" y2="16" stroke="#e27719" stroke-width="3"/>
      </svg>
    </header>

    <div class="watermark-circle" aria-hidden="true"></div>

    <div class="name-tab">
      <h1 class="person-name">Marion Tadwick</h1>
    </div>

    <ul class="contact-list">
      <li class="contact-item">
        <svg class="contact-icon" viewBox="0 0 24 24" aria-label="Telephone">
          <path d="M3 7c0-2 2-3 9-3s9 1 9 3v2h-5V7.5c-1-.4-2.5-.5-4-.5s-3 .1-4 .5V9H3z"/>
          <path d="M7 10h10l3 6v4H4v-4zM12 12.5a2.5 2.5 0 1 0 0 5a2.5 2.5 0 0 0 0-5z" fill-rule="evenodd"/>
        </svg>
        <span class="contact-text">07382 415067</span>
      </li>
      <li class="contact-item">
        <svg class="contact-icon" viewBox="0 0 24 24" aria-label="Email">
          <path d="M2 5h20v14H2zM4 7v.6l8 5.6 8-5.6V7zM4 10v7h16v-7l-8 5.6z" fill-rule="evenodd"/>
        </svg>
        <span class="contact-text">mtadwick@brontlearn.co.uk</span>
      </li>
      <li class="contact-item">
        <svg class="contact-icon" viewBox="0 0 24 24" aria-label="Website">
          <circle cx="12" cy="12" r="10" fill="none" stroke="#e27719" stroke-width="2"/>
          <ellipse cx="12" cy="12" rx="4.5" ry="10" fill="none" stroke="#e27719" stroke-width="1.8"/>
          <line x1="2" y1="12" x2="22" y2="12" stroke="#e27719" stroke-width="1.8"/>
          <line x1="4" y1="7" x2="20" y2="7" stroke="#e27719" stroke-width="1.5"/>
          <line x1="4" y1="17" x2="20" y2="17" stroke="#e27719" stroke-width="1.5"/>
        </svg>
        <span class="contact-text">www.brontlearn.co.uk.</span>
      </li>
    </ul>
  </article>
</body>
</html>
```